Modern Business Card

Modern professional business card with more than just logo and demographic info. Something memorable.

We are a trendy/modern chiropractic group with an emphasis on neurology, hence the minimalist-type brain logo. We want to convey that modern and technical aspect with professionalism and the elite nature of our practice environment.

```html
<!DOCTYPE html>
<html lang="en">
<head>
<meta charset="utf-8">
<title>Northvale Chiropractic – Business Card</title>
<link href="https://fonts.googleapis.com/css2?family=Montserrat:wght@400;500&family=Oswald:wght@500&display=swap" rel="stylesheet">
<style>
  :root {
    --backdrop: #2b2b2d;
    --card: #1b1b1d;
    --emboss: #2a2a2d;
    --accent: #4b86c9;
    --ink: #f2f2f2;
    --rule: #9a9a9a;
  }
  * { box-sizing: border-box; margin: 0; padding: 0; }
  html, body {
    width: 1200px; height: 900px; overflow: hidden;
    background: var(--backdrop);
  }
  .canvas {
    position: relative; width: 1200px; height: 900px;
  }
  .card {
    position: absolute; left: 300px;
    width: 600px; height: 343px;
    background: var(--card);
    border-radius: 16px;
    box-shadow: 0 14px 30px rgba(0,0,0,.45);
  }
  .card--front { top: 87px; }
  .card--back { top: 470px; }

  /* front */
  .brand {
    position: absolute; inset: 0;
    display: flex; align-items: center; justify-content: center; gap: 18px;
  }
  .brand__dot {
    width: 26px; height: 26px; border-radius: 50%;
    background: var(--emboss);
  }
  .brand__name {
    font-family: "Montserrat", sans-serif; font-weight: 500;
    font-size: 30px; letter-spacing: 4px; text-transform: uppercase;
    color: var(--emboss); line-height: 1.15;
  }

  /* back */
  .person {
    position: absolute; left: 70px; top: 105px; width: 205px;
    text-align: right;
  }
  .person__name {
    font-family: "Oswald", sans-serif; font-weight: 500;
    font-size: 32px; letter-spacing: 3px; color: var(--accent);
    text-transform: uppercase; line-height: 1.1;
  }
  .person__role {
    font-family: "Montserrat", sans-serif; font-size: 16px;
    color: var(--ink); margin-top: 2px;
  }
  .divider {
    position: absolute; left: 300px; top: 108px;
    width: 1px; height: 90px; background: var(--rule);
  }
  .contacts {
    position: absolute; left: 322px; top: 112px;
    list-style: none;
    font-family: "Montserrat", sans-serif; font-size: 16px; color: var(--ink);
  }
  .contacts li {
    display: flex; align-items: center; gap: 12px; height: 27px;
  }
  .contacts svg { width: 15px; height: 15px; flex: none; }
  .address {
    position: absolute; left: 0; right: 0; top: 262px;
    display: flex; align-items: center; justify-content: center; gap: 12px;
    font-family: "Montserrat", sans-serif; font-size: 16px; color: var(--ink);
  }
  .address__mark {
    width: 12px; height: 12px; border-radius: 50%; background: var(--accent);
  }
</style>
</head>
<body>
<main class="canvas">
  <section class="card card--front" aria-label="Card front">
    <div class="brand">
      <span class="brand__dot"></span>
      <span class="brand__name">Northvale<br>Chiropractic</span>
    </div>
  </section>

  <section class="card card--back" aria-label="Card back">
    <div class="person">
      <p class="person__name">Marcus Ellery</p>
      <p class="person__role">Director</p>
    </div>
    <span class="divider"></span>
    <ul class="contacts">
      <li>
        <svg viewBox="0 0 16 16" fill="none" stroke="var(--accent)" stroke-width="1.5"><path d="M4 1.5 L6.5 4.5 L5 6.5 Q6.5 9.5 9.5 11 L11.5 9.5 L14.5 12 L13 14.5 Q6 14 1.5 3 Z"/></svg>
        (555) 318-2046
      </li>
      <li>
        <svg viewBox="0 0 16 16" fill="none" stroke="var(--accent)" stroke-width="1.4"><rect x="1.5" y="3.5" width="13" height="9" rx="1"/><path d="M1.5 4 L8 9 L14.5 4"/></svg>
        hello@northvalechiro.com
      </li>
      <li>
        <svg viewBox="0 0 16 16" fill="none" stroke="var(--accent)" stroke-width="1.3"><circle cx="8" cy="8" r="6.5"/><ellipse cx="8" cy="8" rx="2.8" ry="6.5"/><path d="M1.5 8 H14.5 M2.5 4.8 H13.5 M2.5 11.2 H13.5"/></svg>
        www.northvalechiro.com
      </li>
    </ul>
    <p class="address"><span class="address__mark"></span>1187 Larkspur Bend Corvallis, OR 97330</p>
  </section>
</main>
</body>
</html>
```